Chimney Service company needs new business card design

We need a updated business card with our new logo added. We provide a full range of chimney services throughout Vermont and New Hampshire. The business card will be one sided and color. Attached is our current business card another document showing all the information we would like on the card.
We dont like a lot of flashy colors.... here is a link to our website to get an idea of our branding www.flueguardianvt.example

Target Market(s)

homeowners

Industry/Entity Type

Business

Contact Information for Business Card

See attached sheet for content.

Font styles to use
Serif
Sans Serif

Requirements
Must have
• all information provided on separate sheet
Should not have
• Additional information that may clogg up design

```html
<!DOCTYPE html>
<html lang="en">
<head>
<meta charset="utf-8">
<title>Flue Guardian — Business Card</title>
<link rel="stylesheet" href="https://fonts.googleapis.com/css2?family=Cinzel:wght@400;600&family=Lato:wght@400;700&display=swap">
<style>
  :root {
    --page-bg: #2b2b2b;
    --card-bg: #ffffff;
    --ink: #2a2a2a;
    --brand-red: #a51c22;
    --band-text: #ffffff;
  }
  * { margin: 0; padding: 0; box-sizing: border-box; }
  html, body { width: 1200px; height: 738px; overflow: hidden; background: var(--page-bg); }
  .card {
    position: absolute; left: 75px; top: 69px; width: 1050px; height: 600px;
    background: var(--card-bg); color: var(--ink);
    font-family: "Lato", "Helvetica Neue", Arial, sans-serif;
  }
  .brand {
    position: absolute; left: 40px; top: 120px; width: 400px;
    display: flex; flex-direction: column; align-items: center; gap: 30px;
  }
  .brand-square { width: 150px; height: 150px; border: 14px solid var(--ink); }
  .brand-name {
    font-family: "Cinzel", Georgia, serif; font-weight: 600; font-size: 44px;
    color: var(--ink); letter-spacing: 1px; white-space: nowrap;
  }
  .divider {
    position: absolute; left: 480px; top: 75px; width: 3px; height: 300px;
    background: var(--brand-red);
  }
  .contact { position: absolute; left: 515px; top: 62px; list-style: none; }
  .contact li { display: flex; align-items: center; gap: 14px; font-size: 21px; line-height: 32px; }
  .contact svg { width: 16px; height: 16px; fill: var(--brand-red); flex: none; }
  .services { position: absolute; left: 515px; top: 175px; }
  .services-title {
    font-family: "Cinzel", Georgia, serif; font-weight: 600; font-size: 28px;
    color: var(--brand-red); margin-bottom: 6px;
  }
  .services-list { list-style: none; font-size: 22px; line-height: 31px; }
  .service-area {
    position: absolute; left: 0; right: 0; top: 450px; text-align: center;
    font-family: "Cinzel", Georgia, serif; font-size: 24px; letter-spacing: 0.5px;
  }
  .service-area .since { color: var(--brand-red); font-family: "Lato", Arial, sans-serif; font-size: 22px; }
  .promise-band {
    position: absolute; left: 0; right: 0; bottom: 0; height: 82px;
    background: var(--brand-red); color: var(--band-text);
    display: flex; align-items: center; justify-content: center;
    font-family: "Cinzel", Georgia, serif; font-size: 25px; letter-spacing: 0.5px;
  }
</style>
</head>
<body>
  <article class="card">
    <div class="brand">
      <div class="brand-square"></div>
      <div class="brand-name">Flue Guardian</div>
    </div>

    <div class="divider"></div>

    <ul class="contact">
      <li><svg viewBox="0 0 16 16"><path d="M3 1l3 3-1.5 2a9 9 0 0 0 5.5 5.5L12 10l3 3-2 2C6 15 1 10 1 3z"/></svg>802-555-0147</li>
      <li><svg viewBox="0 0 16 16"><path d="M1 3h14v2L8 9 1 5zM1 7l7 4 7-4v6H1z"/></svg>info@flueguardianvt.example</li>
      <li><svg viewBox="0 0 16 16"><path d="M8 1a7 7 0 1 0 0 14A7 7 0 0 0 8 1zm0 2a5 5 0 0 1 0 10A5 5 0 0 1 8 3z"/><rect x="2" y="7" width="12" height="2"/><rect x="7" y="2" width="2" height="12"/></svg>www.flueguardianvt.example</li>
    </ul>

    <section class="services">
      <h2 class="services-title">Services We Provide</h2>
      <ul class="services-list">
        <li>Full Masonry Services</li>
        <li>Historic chimney restoration</li>
        <li>Stainless steel liners</li>
        <li>New Chimney installations</li>
        <li>KVSG Certified Chimney sweeps</li>
      </ul>
    </section>

    <p class="service-area">Serving VT and Northern NY<span class="since">–since 2004</span></p>

    <div class="promise-band">Fully Insured–Free Estimates | Family Owned and Operated</div>
  </article>
</body>
</html>
```